3D Printing Website redesign

We are in the process of redesigning our website. Attached is an image of one of the proposed pages - "The Quillmarrow". The idea with this page is that site visitors can get an indicative estimate of the cost of 3D Printing based on some provided metrics. When the user alters the metrics the price changes accordingly. We are looking for a design to support this page that will also be used across our site.

Reason: Allow more time for designers to submit designs

Reason: Still looking for the design to blow us away!

Printing

```html
<!DOCTYPE html>
<html lang="en">
<head>
<meta charset="utf-8">
<title>Layerform Studio</title>
<link rel="stylesheet" href="https://fonts.googleapis.com/css2?family=Open+Sans:wght@400;600;700;800&display=swap">
<style>
  :root {
    --paper: #f3f3f3;
    --navy: #22477f;
    --navy-dark: #1b3a6b;
    --band: #253f6d;
    --cyan: #10b5ee;
    --field: #e3e6ef;
    --ink-grey: #7f7f7f;
    --placeholder: #7a7a7a;
    --brand-blue: #1376cc;
    --white: #ffffff;
  }
  * { margin: 0; padding: 0; box-sizing: border-box; }
  html, body { width: 1200px; height: 557px; overflow: hidden; }
  body {
    position: relative;
    font-family: "Open Sans", sans-serif;
    background: var(--paper);
  }
  .contact {
    position: absolute; left: 126px; top: 11px;
    font-size: 14px; line-height: 17.6px; color: var(--ink-grey);
    list-style: none;
  }
  .main-nav {
    position: absolute; left: 0; top: 112px; width: 1200px; height: 57px;
    background: linear-gradient(var(--navy), var(--navy-dark));
    box-shadow: 0 2px 4px rgba(0,0,0,.25);
  }
  .main-nav ul { list-style: none; display: flex; position: absolute; left: 103px; top: 0; height: 57px; }
  .main-nav li {
    height: 57px; display: flex; align-items: center; padding: 0 16px;
    color: var(--white); font-size: 15px; font-weight: 600;
    border-right: 1px solid rgba(255,255,255,.12);
  }
  .main-nav li.is-active { background: var(--cyan); border-right: 0; }
  .main-nav li.nav-right { position: absolute; left: 595px; border: 0; }
  .brand-mark {
    position: absolute; left: 492px; top: 8px; width: 196px; height: 196px;
    border-radius: 50%; background: #b9bec6; box-shadow: 0 4px 10px rgba(0,0,0,.3);
  }
  .brand-name {
    position: absolute; left: 0; top: 228px; width: 1200px; text-align: center;
    font-size: 112px; font-weight: 800; color: var(--brand-blue); letter-spacing: -2px;
  }
  .account-tab {
    position: absolute; left: 1047px; top: 0; width: 50px; height: 48px; background: var(--cyan);
    display: flex; align-items: center; justify-content: center;
  }
  .login-panel {
    position: absolute; left: 767px; top: 48px; width: 330px; height: 152px;
    background: var(--cyan); box-shadow: 0 3px 6px rgba(0,0,0,.3);
  }
  .field {
    position: absolute; left: 22px; width: 286px; height: 33px; background: var(--field);
    font-size: 15px; color: #2a2a2a; padding: 6px 14px;
  }
  .field.is-focused { border: 1px solid var(--navy-dark); }
  .btn {
    position: absolute; top: 97px; width: 127px; height: 33px; background: var(--navy);
    color: var(--white); font-size: 15px; display: flex; align-items: center; justify-content: center;
  }
  .lost-password {
    position: absolute; left: 43px; top: 134px; font-size: 9px; font-weight: 700; color: var(--white);
  }
  .content-band {
    position: absolute; left: 0; top: 415px; width: 1200px; height: 142px; background: var(--band);
  }
  .content-slot {
    position: absolute; left: 182px; top: 38px; width: 835px; height: 104px; background: var(--placeholder);
  }
</style>
</head>
<body>
  <ul class="contact">
    <li>Layerform Studio</li>
    <li>Shop 2, 14 Harbour Lane, Millers Point, Sydney 2000</li>
    <li>Ph: 61 2 5550 1234</li>
    <li>M: 0400 555 018</li>
    <li>e-mail: hello@layerformstudio.com.au</li>
  </ul>

  <nav class="main-nav">
    <ul>
      <li class="is-active">HOME</li>
      <li>SHOP</li>
      <li>PRICES</li>
      <li>MATERIALS</li>
      <li class="nav-right">GALLERY</li>
    </ul>
  </nav>

  <div class="brand-mark" aria-hidden="true"></div>
  <div class="brand-name">Layerform Studio</div>

  <section class="content-band">
    <div class="content-slot"></div>
  </section>

  <div class="account-tab">
    <svg width="24" height="22" viewBox="0 0 24 22" aria-hidden="true">
      <circle cx="12" cy="6.5" r="5.5" fill="#fff"/>
      <path d="M1 22c0-6 5-9 11-9s11 3 11 9z" fill="#fff"/>
    </svg>
  </div>
  <form class="login-panel">
    <div class="field is-focused" style="top:14px">E-mail</div>
    <div class="field" style="top:55px">Password</div>
    <div class="btn" style="left:23px">LOGIN</div>
    <div class="btn" style="left:181px">REGISTER</div>
    <div class="lost-password">LOST PASSWORD?</div>
  </form>
</body>
</html>
```